Gutschein-Design für Verkauf von Online-Schmuckstücken
Zielgruppe
Wir verkaufen Online Schmuckstücke!
www.silberfaden-shop.de
Aufgabenstellung
Wir haben eine schwarze Schachtel erstellt und da drinne wird eine Geschenkgutschein sein:
Es soll sehr schlicht sein und schwarzen Hintergrund haben.
Vorderseite nur unser LOGO.
Rückseite:
Betrag: _________
Gültig Bis: _________
Code: __________
Und unten klein gedruckt steht:
Diese Karte ist gültig nur auf der online shop seite www.silberfaden-shop.de und in unserer offizielen Stores. Dieses Karte ist nicht gültig bei rabatierte Produkten und man kann nicht mit dieser karte einen Gutscheinkarte kaufen.
Der Design soll sehr schlicht und dezenz sein.

```html
<!DOCTYPE html>
<html lang="de">
<head>
<meta charset="utf-8">
<title>Silberfaden – Geschenkgutschein</title>
<link rel="stylesheet" href="https://fonts.googleapis.com/css2?family=Open+Sans:wght@400&display=swap">
<style>
  :root {
    --backdrop: #d9d9d9;
    --card-dark: #000000;
    --card-light: #ffffff;
    --ink: #111111;
    --ink-on-dark: #ffffff;
  }
  * { box-sizing: border-box; margin: 0; padding: 0; }
  html, body {
    width: 848px;
    height: 1200px;
    overflow: hidden;
    background: var(--backdrop);
    font-family: "Open Sans", Arial, sans-serif;
  }
  .canvas {
    position: relative;
    width: 848px;
    height: 1200px;
  }

  /* Front side */
  .card-front {
    position: absolute;
    left: 184px;
    top: 63px;
    width: 605px;
    height: 605px;
    background: var(--card-dark);
  }
  .brand-front {
    position: absolute;
    left: 0;
    right: 0;
    top: 208px;
    display: flex;
    flex-direction: column;
    align-items: center;
    gap: 22px;
  }
  .brand-front .brand-dot {
    width: 100px;
    height: 100px;
    border-radius: 50%;
    background: var(--ink-on-dark);
  }
  .brand-front .brand-name {
    color: var(--ink-on-dark);
    font-size: 44px;
    font-weight: 400;
    letter-spacing: 1px;
    line-height: 1;
  }

  /* Back side */
  .card-back {
    position: absolute;
    left: 60px;
    top: 520px;
    width: 620px;
    height: 620px;
    background: var(--card-light);
  }
  .brand-back {
    position: absolute;
    left: 0;
    right: 0;
    top: 101px;
    display: flex;
    justify-content: center;
  }
  .brand-back .brand-dot {
    width: 52px;
    height: 52px;
    border-radius: 50%;
    background: var(--card-dark);
  }
  .voucher-fields {
    position: absolute;
    left: 0;
    top: 282px;
    width: 100%;
  }
  .voucher-field {
    display: flex;
    align-items: flex-end;
    height: 40px;
  }
  .voucher-field .label {
    width: 238px;
    padding-right: 12px;
    text-align: right;
    font-size: 12px;
    letter-spacing: 0.6px;
    color: var(--ink);
    line-height: 1;
  }
  .voucher-field .fill-line {
    width: 226px;
    border-bottom: 1px solid var(--ink);
    margin-bottom: 2px;
  }
  .fine-print {
    position: absolute;
    left: 0;
    right: 0;
    bottom: 62px;
    text-align: center;
    font-size: 8px;
    line-height: 1.3;
    color: var(--ink);
  }
</style>
</head>
<body>
  <main class="canvas">
    <section class="card-front" aria-label="Gutschein Vorderseite">
      <div class="brand-front">
        <span class="brand-dot" aria-hidden="true"></span>
        <span class="brand-name">Silberfaden</span>
      </div>
    </section>

    <section class="card-back" aria-label="Gutschein Rückseite">
      <div class="brand-back">
        <span class="brand-dot" aria-hidden="true"></span>
      </div>

      <div class="voucher-fields">
        <div class="voucher-field">
          <span class="label">Betrag</span>
          <span class="fill-line"></span>
        </div>
        <div class="voucher-field">
          <span class="label">Gültig bis</span>
          <span class="fill-line"></span>
        </div>
        <div class="voucher-field">
          <span class="label">Code</span>
          <span class="fill-line"></span>
        </div>
      </div>

      <p class="fine-print">
        Diese Karte ist gültig in unserem Onlineshop: www.silberfaden-shop.de und in unseren offiziellen Stores.<br>
        Dieses Karte ist nicht einzulösen bei rabattierten Produkten und beim Kauf einer Gutscheinkarte.
      </p>
    </section>
  </main>
</body>
</html>
```